Process Flow Chart for Real Estate Agency

We need a visual flow chart of the process of selling a home for our Real Estate Agency. This visual will be provided to all new staff to explain the process and also to potential clients to explain how detailed the process is. It needs to show each step as detailed in the attached word doc and use icons and arrows to show the direction of flow.

Target Market(s)

Staff & Potential Clients

Industry/Entity Type

Real Estate

Font styles to use
Sans Serif

Colors

Designer to choose colors to be used in the design.

Requirements
Must have
• Easy to read, lots of icons, colour coded with Agent in one colour, Admin in another (some tasks are either/or so not sure what to colour those ones.)
Nice to have
• Include one of the two attached logos

```html
<!DOCTYPE html>
<html lang="en">
<head>
<meta charset="utf-8">
<title>Hartwell Partners Real Estate – Task Catalog</title>
<link rel="stylesheet" href="https://fonts.googleapis.com/css2?family=Source+Sans+3:wght@400;600;700&display=swap">
<style>
  :root {
    --backdrop: #e2e2e2;
    --page: #f4f4f4;
    --sketch: #e9e9e9;
    --ink: #3a3a3a;
    --track: #2f2f2f;
    --agent: #1f8fd6;
    --admin: #f39214;
    --label-bg: #1c1c1c;
    --white: #ffffff;
  }
  * { box-sizing: border-box; margin: 0; padding: 0; }
  html, body { width: 1200px; height: 835px; overflow: hidden; }
  body {
    background: var(--backdrop);
    font-family: "Source Sans 3", sans-serif;
    color: var(--ink);
    position: relative;
  }

  .spread {
    position: absolute; left: 0; top: 256px;
    width: 664px; height: 324px;
    overflow: hidden;
    background: var(--page);
  }
  .page-backdrop {
    position: absolute; inset: 0;
    background: linear-gradient(180deg, var(--page) 0%, var(--sketch) 100%);
  }
  .gutter {
    position: absolute; left: 219px; top: 0; bottom: 0; width: 3px;
    background: linear-gradient(90deg, rgba(0,0,0,0.05), rgba(0,0,0,0));
  }

  /* History page (left, runs off canvas edge) */
  .history {
    position: absolute; left: -22px; top: 46px; width: 212px;
    font-size: 8.2px; line-height: 10.3px;
    text-align: justify; color: #333;
  }
  .history p { margin-bottom: 10.5px; }

  /* Process page */
  .flow-track {
    position: absolute; left: 236px; top: 5px;
    width: 135px; height: 292px;
  }
  .task-list {
    position: absolute; left: 377px; top: 14px; width: 272px;
    list-style: none;
    font-size: 7.3px; line-height: 9px;
  }
  .task-list li { margin-bottom: 2.6px; }
  .role-agent { color: var(--agent); }
  .role-admin { color: var(--admin); }
  .page-number {
    position: absolute; right: 10px; bottom: 6px;
    font-size: 5.5px; color: #888;
  }

  /* Cover */
  .cover {
    position: absolute; left: 686px; top: 257px;
    width: 440px; height: 323px; overflow: hidden;
  }
  .cover-photo {
    position: absolute; inset: 0;
    background:
      linear-gradient(180deg, rgba(255,255,255,0) 70%, rgba(236,236,236,0.85) 100%),
      linear-gradient(100deg, #8a7a66 0%, #b5a285 18%, #e6d8c8 34%, #f1e9df 46%, #9fb6cf 62%, #b9c9db 78%, #e4e1dc 100%);
  }
  .brand {
    position: absolute; right: 10px; top: 18px;
    display: flex; align-items: flex-start; gap: 5px;
  }
  .brand-mark {
    width: 10px; height: 10px; border-radius: 50%;
    background: var(--admin); margin-top: 4px;
  }
  .brand-name {
    font-weight: 600; color: #2b2b2b; line-height: 1; text-align: left;
  }
  .brand-name .line-1 { display: block; font-size: 16px; }
  .brand-name .line-2 { display: block; font-size: 10px; margin-top: 3px; }
  .cover-title {
    position: absolute; right: 10px; top: 75px;
    background: var(--label-bg); color: var(--white);
    font-size: 15.5px; font-weight: 600; line-height: 1; letter-spacing: 0.2px;
    padding: 4px 5px 4px;
  }
</style>
</head>
<body>

<section class="spread">
  <div class="page-backdrop" role="img" aria-label="Faint sketched streetscape of houses behind the page content"></div>
  <div class="gutter"></div>

  <div class="history">
    <p>On 5th August 2013 when husband and wife team started the business in a humble but functional office space, it grew so much that they relocated to their first "real" office. They celebrated their first birthday and their Grand Opening and continued to grow since that time.</p>
    <p>After working with one of Adelaide's Premier Real Estate agencies in its department as a Property Inspector, Daniel soon was awarded "Leasing Manager of The Year".</p>
    <p>Moving into a Sales role. In his first year, Daniel achieved and received recognition for the sale of his first million dollar "Dollar Club". In 2009, Daniel invited his wife Mara and the Hartwell Team was born! In 2011, The Hartwell Team took the team to one of Australia's largest franchises, the number one office in South Australia.</p>
    <p>A boutique agency and then a large franchise office they required to go out on their own and create Hartwell</p>
    <p>Partners and - with staff specialising in sales, property strategy and marketing. Hartwell Partners Real Estate won in the category of Best New Office 2015 in the state finalists in the category of Best Small Agency</p>
  </div>

  <svg class="flow-track" viewBox="0 0 180 390" aria-label="Flow of twenty tasks, blue for agent, orange for admin">
    <defs>
      <g id="icon-doc"><rect x="-4.5" y="-5.5" width="9" height="11" rx="1" fill="none" stroke="#fff" stroke-width="1.4"/><path d="M-2.5-2h5M-2.5 0.5h5M-2.5 3h3.5" stroke="#fff" stroke-width="1.1"/></g>
      <g id="icon-cal"><rect x="-5.5" y="-4.5" width="11" height="10" rx="1" fill="none" stroke="#fff" stroke-width="1.4"/><path d="M-5.5-1.5h11M-2-6.5v3M2-6.5v3" stroke="#fff" stroke-width="1.2"/></g>
      <g id="icon-chat"><path d="M-6-4h12v7h-7l-3 3v-3h-2z" fill="none" stroke="#fff" stroke-width="1.3" stroke-linejoin="round"/></g>
      <g id="icon-phone"><rect x="-3.5" y="-6" width="7" height="12" rx="1.5" fill="none" stroke="#fff" stroke-width="1.4"/><circle cx="0" cy="3.6" r="0.9" fill="#fff"/></g>
      <g id="icon-star"><path d="M0-6l1.8 3.8 4.2.5-3.1 2.9.8 4.1L0 3.3l-3.7 2 .8-4.1-3.1-2.9 4.2-.5z" fill="none" stroke="#fff" stroke-width="1.2" stroke-linejoin="round"/></g>
      <g id="icon-list"><path d="M-2-4h7M-2 0h7M-2 4h7" stroke="#fff" stroke-width="1.4"/><circle cx="-5" cy="-4" r="1" fill="#fff"/><circle cx="-5" cy="0" r="1" fill="#fff"/><circle cx="-5" cy="4" r="1" fill="#fff"/></g>
      <g id="icon-search"><circle cx="-1.2" cy="-1.2" r="4" fill="none" stroke="#fff" stroke-width="1.5"/><path d="M1.8 1.8l4 4" stroke="#fff" stroke-width="1.7"/></g>
      <g id="icon-at"><circle cx="0" cy="0" r="2.4" fill="none" stroke="#fff" stroke-width="1.3"/><path d="M2.4 0v1.5a2 2 0 0 0 4 0V0a6 6 0 1 0-2.4 4.8" fill="none" stroke="#fff" stroke-width="1.3"/></g>
    </defs>

    <path d="M30,22 H140 A19.25,19.25 0 0 1 140,60.5 H30 A19.25,19.25 0 0 0 30,99 H140 A19.25,19.25 0 0 1 140,137.5 H30 A19.25,19.25 0 0 0 30,176 H140 A19.25,19.25 0 0 1 140,214.5 H30 A19.25,19.25 0 0 0 30,253 H140 A19.25,19.25 0 0 1 140,291.5 H30 A19.25,19.25 0 0 0 30,330 H140 A19.25,19.25 0 0 1 140,368.5 H30"
          fill="none" stroke="var(--track)" stroke-width="6"/>

    <g class="nodes">
      <g transform="translate(30,22)"><circle r="12" fill="var(--agent)" stroke="#fff" stroke-width="2"/><use href="#icon-phone"/></g>
      <g transform="translate(140,22)"><circle r="12" fill="var(--agent)" stroke="#fff" stroke-width="2"/><use href="#icon-star"/></g>
      <g transform="translate(140,60.5)"><circle r="12" fill="var(--agent)" stroke="#fff" stroke-width="2"/><use href="#icon-phone"/></g>
      <g transform="translate(30,60.5)"><circle r="12" fill="var(--agent)" stroke="#fff" stroke-width="2"/><use href="#icon-cal"/></g>
      <g transform="translate(30,99)"><circle r="12" fill="var(--agent)" stroke="#fff" stroke-width="2"/><use href="#icon-chat"/></g>
      <g transform="translate(140,99)"><circle r="12" fill="var(--agent)" stroke="#fff" stroke-width="2"/><use href="#icon-list"/></g>
      <g transform="translate(140,137.5)"><circle r="12" fill="var(--agent)" stroke="#fff" stroke-width="2"/><use href="#icon-list"/></g>
      <g transform="translate(30,137.5)"><circle r="12" fill="var(--admin)" stroke="#fff" stroke-width="2"/><use href="#icon-doc"/></g>
      <g transform="translate(30,176)"><circle r="12" fill="var(--admin)" stroke="#fff" stroke-width="2"/><use href="#icon-star"/></g>
      <g transform="translate(140,176)"><circle r="12" fill="var(--admin)" stroke="#fff" stroke-width="2"/><use href="#icon-doc"/></g>
      <g transform="translate(140,214.5)"><circle r="12" fill="var(--admin)" stroke="#fff" stroke-width="2"/><use href="#icon-list"/></g>
      <g transform="translate(30,214.5)"><circle r="12" fill="var(--admin)" stroke="#fff" stroke-width="2"/><use href="#icon-cal"/></g>
      <g transform="translate(30,253)"><circle r="12" fill="var(--agent)" stroke="#fff" stroke-width="2"/><use href="#icon-chat"/></g>
      <g transform="translate(140,253)"><circle r="12" fill="var(--agent)" stroke="#fff" stroke-width="2"/><use href="#icon-cal"/></g>
      <g transform="translate(140,291.5)"><circle r="12" fill="var(--admin)" stroke="#fff" stroke-width="2"/><use href="#icon-doc"/></g>
      <g transform="translate(30,291.5)"><circle r="12" fill="var(--agent)" stroke="#fff" stroke-width="2"/><use href="#icon-star"/></g>
      <g transform="translate(30,330)"><circle r="12" fill="var(--agent)" stroke="#fff" stroke-width="2"/><use href="#icon-doc"/></g>
      <g transform="translate(140,330)"><circle r="12" fill="var(--admin)" stroke="#fff" stroke-width="2"/><use href="#icon-list"/></g>
      <g transform="translate(140,368.5)"><circle r="12" fill="var(--admin)" stroke="#fff" stroke-width="2"/><use href="#icon-search"/></g>
      <g transform="translate(30,368.5)"><circle r="12" fill="var(--admin)" stroke="#fff" stroke-width="2"/><use href="#icon-at"/></g>
    </g>
  </svg>

  <ol class="task-list">
    <li>1 <span class="role-agent">Agent</span> calls potential client to arrange a time to meet and obtain<br>details about the property</li>
    <li>2 <span class="role-agent">Agent</span> ensures all decision makers will be present at meeting</li>
    <li>3 <span class="role-agent">Agent</span> adds vendors contact details on phone</li>
    <li>4 <span class="role-agent">Agent</span> adds appointment to personal calendar</li>
    <li>5 <span class="role-agent">Agent</span> sends SMS to potential client to thank them for the opportunity</li>
    <li>6 <span class="role-agent">Agent</span>/<span class="role-admin">Admin</span> orders ARE from Brookfield's</li>
    <li>7 <span class="role-agent">Agent</span> completes a TMP to provide to Admin for Prelisting kit prep</li>
    <li>8 <span class="role-admin">Admin</span> prepares pre-listing kit with questionnaire, sample<br>brochure &amp; cover letter, property magazine, agent profile booklet</li>
    <li>9 <span class="role-admin">Admin</span>/<span class="role-agent">Agent</span> delivers pre-listing kit (preferably within the hour)<br>&amp; SMS potential vendor</li>
    <li>10 <span class="role-admin">Admin</span>/<span class="role-agent">Agent</span> to research &amp; prints comparable Sales reports</li>
    <li>11 <span class="role-admin">Admin</span> prepares TMP with Marketing Costs Selection booklet, Service<br>Offering Selection booklet, Sales Agency Agreement &amp; Benefits Form, ARE</li>
    <li>12 <span class="role-admin">Admin</span> enters potential Vendor into CRM &amp; set "Appraisal" Track</li>
    <li>13 <span class="role-agent">Agent</span> confirms appraisal on the morning of the appointment with an SMS</li>
    <li>14 <span class="role-agent">Agent</span> meets with potential Vendor and completes the appraisal</li>
    <li>15 <span class="role-admin">Admin</span> prepares written appraisal report hand-deliver with coffee<br>vouchers &amp;/or gift</li>
    <li>16 <span class="role-agent">Agent</span> hand-delivers report with coffee voucher or Larkin chocolates</li>
    <li>17 <span class="role-agent">Agent</span> receives confirmation from vendor to proceed with listing &amp; arranges<br>signing of Residential Sales Agency Agreement</li>
    <li>18 <span class="role-admin">Admin</span> checks Residential Sales Agency &amp; enters as Listing into CRM</li>
    <li>19 <span class="role-admin">Admin</span> completes the "New Listing Checklist" and prepares black folder</li>
    <li>20 <span class="role-admin">Admin</span> checks for Vendor email addresses &amp; if required call or SMS<br>client to obtain</li>
  </ol>

  <span class="page-number">2</span>
</section>

<section class="cover">
  <div class="cover-photo" role="img" aria-label="Photograph of a smiling couple meeting with an agent at a table with house plans"></div>
  <div class="brand">
    <span class="brand-mark"></span>
    <span class="brand-name"><span class="line-1">Hartwell Partners</span><span class="line-2">Real Estate</span></span>
  </div>
  <h1 class="cover-title">TASK CATALOG</h1>
</section>

</body>
</html>
```